Coastline Premier Retreats Business Card Design

Design a business card for Coastline Premier Retreats. Look at the website for colors and reference. Card should have logo, name, title, office number, mobile number, email, URL and a tagline like, "Luxury Hotel & Resort Email Marketing" (This might change).

https://www.coastlinepremierretreats.example

The rest I will leave up to your imagination.

Contact Information for Business Card

Logo, name, title, office number, mobile number, email, URL and a tagline like, "Luxury Hotel & Resort Email Marketing" (This might change).

```html
<!DOCTYPE html>
<html lang="en">
<head>
<meta charset="utf-8">
<title>Coastline Premier Retreats — Business Card</title>
<link rel="stylesheet" href="https://fonts.googleapis.com/css2?family=Arimo:wght@400;700&display=swap">
<style>
  :root {
    --bg: #1e1e1e;
    --card: #161616;
    --accent: #e8731a;
    --ink: #f2f2f2;
  }
  * { margin: 0; padding: 0; box-sizing: border-box; }
  html, body {
    width: 1200px; height: 1059px; overflow: hidden;
    background: var(--bg);
    font-family: "Arimo", Arial, sans-serif;
    color: var(--ink);
  }
  .canvas { position: relative; width: 1200px; height: 1059px; }
  .card {
    position: absolute;
    background: var(--card);
    box-shadow: 0 10px 24px rgba(0,0,0,0.6);
  }
  .card--front { left: 256px; top: 89px; width: 688px; height: 390px; }
  .card--back  { left: 254px; top: 547px; width: 693px; height: 394px; }

  .brand {
    position: absolute; display: flex; align-items: center;
    font-family: "Arimo", Arial, sans-serif; font-weight: 700;
    color: var(--ink); white-space: nowrap;
  }
  .brand__mark { background: var(--accent); flex: none; }

  .card--front .brand { left: 40px; top: 176px; gap: 10px; font-size: 20px; }
  .card--front .brand__mark { width: 12px; height: 12px; }

  .card--back .brand { left: 0; right: 0; top: 172px; justify-content: center; gap: 18px; font-size: 40px; }
  .card--back .brand__mark { width: 22px; height: 22px; }

  .divider { position: absolute; left: 347px; top: 90px; width: 1px; height: 190px; background: var(--accent); }

  .contact { position: absolute; left: 377px; top: 84px; }
  .contact__name { font-weight: 700; font-size: 28px; color: var(--accent); line-height: 1; letter-spacing: 0.01em; }
  .contact__title { font-size: 16px; margin-top: 3px; letter-spacing: 0.03em; }
  .contact__address { font-size: 16px; line-height: 20.5px; margin-top: 14px; }
  .contact__list { list-style: none; margin-top: 12px; font-size: 16px; line-height: 21.5px; }
  .contact__item { display: flex; align-items: center; gap: 8px; }
  .contact__icon { width: 11px; height: 11px; flex: none; fill: var(--accent); }

  .tagline-band {
    position: absolute; left: 0; right: 0; top: 327px; height: 29px;
    background: var(--accent);
    display: flex; align-items: center; justify-content: center;
    font-size: 16.5px; color: #fff;
  }
</style>
</head>
<body>
<div class="canvas">
  <section class="card card--front">
    <div class="brand">
      <span class="brand__mark"></span>
      <span class="brand__name">Coastline Premier Retreats</span>
    </div>

    <div class="divider"></div>

    <div class="contact">
      <h1 class="contact__name">DANIEL REYES</h1>
      <p class="contact__title">CEO/Founder</p>
      <p class="contact__address">Po Box, 456 B Harbor St<br>Seaside Bay, CA 90412</p>
      <ul class="contact__list">
        <li class="contact__item">
          <svg class="contact__icon" viewBox="0 0 12 12" aria-hidden="true"><path d="M3 0h6a1 1 0 0 1 1 1v10a1 1 0 0 1-1 1H3a1 1 0 0 1-1-1V1a1 1 0 0 1 1-1zm0 1.5v7.5h6V1.5zM6 9.8a.8.8 0 1 0 0 1.6.8.8 0 0 0 0-1.6z"/></svg>
          555.214.7300
        </li>
        <li class="contact__item">
          <svg class="contact__icon" viewBox="0 0 12 12" aria-hidden="true"><path d="M0 4c0-1.5 2.5-2.5 6-2.5S12 2.5 12 4v1H9V3.8H3V5H0zM2.5 6h7l1.5 5H1z"/></svg>
          +34 600 555 214
        </li>
        <li class="contact__item">
          <svg class="contact__icon" viewBox="0 0 12 12" aria-hidden="true"><path d="M6 0l6 4.5V12H0V4.5zM1.2 5.2V11h9.6V5.2L6 8.6z"/></svg>
          info@coastlinepremierretreats.example
        </li>
        <li class="contact__item">
          <svg class="contact__icon" viewBox="0 0 12 12" aria-hidden="true"><circle cx="6" cy="6" r="6"/><path d="M3 3.5l2 .5 1 2-1.5 1 .5 2.5-2-1.5zM7.5 2.2l2 1-1 1.5z" fill="#161616"/></svg>
          www.coastlinepremierretreats.example
        </li>
      </ul>
    </div>

    <div class="tagline-band">Luxury Hotel &amp; Resort Email Marketing</div>
  </section>

  <section class="card card--back">
    <div class="brand">
      <span class="brand__mark"></span>
      <span class="brand__name">Coastline Premier Retreats</span>
    </div>
  </section>
</div>
</body>
</html>
```